Career Development Skills | Business Card & Logo Design

We are looking for a business card including logo design for a new Sydney based business called 'Bright Pathwork'.
We offer a range of services that focus on building the Employability or Employment skills for individuals focusing on job seekers and those interested in building skills required to develop their career. Employability skills are required not only to gain employment, but also to progress within an organisation so as to achieve one's potential.
Updates
Target Market(s)
Our client targets include corporates and govt agencies looking to build skills within their current employee base or assist staff in the transition between roles or workplaces.
Industry/Entity Type
Business
Look and feel
Each slider illustrates characteristics of the customer's brand and the style your logo design should communicate.

```html
<!DOCTYPE html>
<html lang="en">
<head>
<meta charset="utf-8">
<title>Bright Pathwork – Business Card</title>
<link rel="stylesheet" href="https://fonts.googleapis.com/css2?family=Alegreya:wght@700;800&display=swap">
<style>
  :root {
    --sky-top: #2f86d4;
    --sky-mid: #8fb9de;
    --mist: #e9ecef;
    --ink: #111111;
    --brand-red: #c8101a;
    --rule: #1b2633;
    --steel-light: #f1f3f5;
    --steel-mid: #b9c0c8;
    --steel-dark: #7e8791;
  }
  html, body {
    margin: 0;
    padding: 0;
    overflow: hidden;
    background: #ffffff;
  }
  .card {
    position: relative;
    width: 1200px;
    height: 686px;
    overflow: hidden;
    background: linear-gradient(to bottom, var(--sky-top) 0%, var(--sky-mid) 35%, var(--mist) 75%, #f6f6f6 100%);
    font-family: "Alegreya", Georgia, serif;
    color: var(--ink);
  }
  .ladder-art {
    position: absolute;
    inset: 0;
    width: 1200px;
    height: 686px;
  }
  .guide-line {
    position: absolute;
    background: var(--rule);
  }
  .guide-line--horizontal { left: 0; top: 55px; width: 1200px; height: 2px; }
  .guide-line--vertical { left: 123px; top: 0; width: 2px; height: 686px; }
  .brand-name {
    position: absolute;
    left: 32px;
    top: 6px;
    margin: 0;
    font-size: 84px;
    font-weight: 800;
    letter-spacing: 3px;
    line-height: 1;
    white-space: nowrap;
    color: var(--brand-red);
  }
  .contact-person {
    position: absolute;
    left: 243px;
    top: 250px;
    margin: 0;
    font-size: 48px;
    font-weight: 700;
    line-height: 1;
    white-space: nowrap;
    text-shadow: 0 0 6px rgba(255,255,255,0.7);
  }
  .contact-lines {
    position: absolute;
    left: 229px;
    top: 330px;
    margin: 0;
    font-size: 38px;
    font-weight: 700;
    line-height: 57px;
    white-space: nowrap;
    text-shadow: 0 0 6px rgba(255,255,255,0.7);
  }
  .contact-lines .label { display: inline-block; }
  .contact-lines .label--phone { width: 122px; }
  .contact-lines .label--fax { width: 97px; }
  .address {
    position: absolute;
    left: 35px;
    top: 498px;
    margin: 0;
    font-size: 26px;
    font-weight: 700;
    line-height: 42.5px;
    font-style: normal;
    white-space: nowrap;
  }
  .web-links {
    position: absolute;
    right: 28px;
    top: 530px;
    margin: 0;
    text-align: right;
    font-size: 38px;
    font-weight: 700;
    line-height: 61px;
    white-space: nowrap;
    text-shadow: 0 0 8px rgba(255,255,255,0.9);
  }
  .web-links .site { margin-right: 60px; }
</style>
</head>
<body>
  <main class="card">
    <svg class="ladder-art" viewBox="0 0 1200 686" role="img" aria-label="Photograph of a tall metal ladder rising into a blue sky, with faint repeated ladders behind it">
      <defs>
        <linearGradient id="steel" x1="0" y1="0" x2="1" y2="0">
          <stop offset="0" stop-color="var(--steel-dark)"/>
          <stop offset="0.3" stop-color="var(--steel-light)"/>
          <stop offset="0.7" stop-color="var(--steel-mid)"/>
          <stop offset="1" stop-color="var(--steel-dark)"/>
        </linearGradient>
      </defs>
      <polygon points="240,0 330,0 560,686 120,686" fill="#ffffff" opacity="0.18"/>
      <polygon points="560,0 640,0 790,686 430,686" fill="#ffffff" opacity="0.18"/>
      <polygon points="900,0 960,0 1200,560 1200,686 1050,686" fill="#ffffff" opacity="0.15"/>
      <polygon points="840,0 886,0 1200,686 577,686" fill="url(#steel)"/>
    </svg>

    <div class="guide-line guide-line--horizontal"></div>
    <div class="guide-line guide-line--vertical"></div>

    <h1 class="brand-name">Bright Pathwork</h1>

    <h2 class="contact-person">Daniel Harrow</h2>
    <p class="contact-lines">
      <span class="label label--phone">Phone:</span>(02) 9417 2250<br>
      <span class="label label--fax">Fax:</span>(02) 9417 2260
    </p>

    <address class="address">
      Level 20<br>
      Harbourline Tower 3<br>
      148 Kestrel Street<br>
      Harbourline, Sydney 2001
    </address>

    <p class="web-links">
      <span class="site">brightpathwork.com.au</span><br>
      <span class="email">daniel@brightpathwork.com.au</span>
    </p>
  </main>
</body>
</html>
```